Business Card Update, need to bring life to the card, two sided color

We need a new business card design, are moving and changing addresses and need a new look, we have the logos already attached but need a new style moving forward. Can incorporate the color of the logo (The Green) as well, maybe a solid back? We deal with safety products revolving around static electricity and safety lighting. Would like to keep same font in second logo as well.

Target Market(s)

Electrical Safety, Lighting

Contact Information for Business Card

Dale Fenwick
Vice President
Office: 770-555-4821
Cell: 770-555-3067
dale@tkfenwick.example
www.tkfenwick.example
4700 West Harbor Boulevard
Suite #150
Roswell, GA 30076

Font styles to use
Serif
Sans Serif

Requirements
Must have
• Since 1918
Nice to have
• Could use the 100 Year Logo for back of card, would like the back of card to be the same green as logo.
Should not have
• No black cards please.

```html
<!DOCTYPE html>
<html lang="en">
<head>
<meta charset="utf-8">
<title>Fenwick Business Card</title>
<link rel="stylesheet" href="https://fonts.googleapis.com/css2?family=Roboto:wght@400;500;700;900&display=swap">
<style>
  :root {
    --brand-green: #009a5b;
    --card-white: #ffffff;
    --page-bg: #e6e8e7;
    --ink-grey: #4a4a4a;
    --on-green: #ffffff;
  }
  * { box-sizing: border-box; margin: 0; padding: 0; }
  html, body {
    width: 1200px; height: 768px; overflow: hidden;
    background: var(--page-bg);
    font-family: "Roboto", sans-serif;
  }
  .sheet {
    width: 1200px; height: 768px;
    display: flex; align-items: center; justify-content: center; gap: 50px;
  }
  .card {
    width: 540px; height: 309px;
    border-radius: 22px;
    position: relative;
    box-shadow: 0 6px 18px rgba(0,0,0,0.18);
  }
  /* Front */
  .card-front { background: var(--card-white); }
  .brand {
    position: absolute; left: 0; right: 0; top: 100px;
    display: flex; align-items: center; justify-content: center; gap: 14px;
  }
  .brand-dot {
    width: 62px; height: 62px; border-radius: 50%;
    background: var(--brand-green);
  }
  .brand-name {
    color: var(--brand-green); font-weight: 900; line-height: 1.05;
  }
  .brand-name .line-main { display: block; font-size: 27px; }
  .brand-name .line-sub { display: block; font-size: 14px; }
  .since {
    position: absolute; left: 0; right: 0; top: 182px;
    text-align: center; font-size: 12px; font-weight: 500;
    letter-spacing: 3px; text-transform: uppercase; color: var(--brand-green);
  }
  .front-web {
    position: absolute; left: 0; right: 0; bottom: 56px;
    text-align: center; font-size: 13px; letter-spacing: 5px; color: var(--ink-grey);
  }
  /* Back */
  .card-back { background: var(--brand-green); color: var(--on-green); }
  .person {
    position: absolute; right: 300px; top: 92px; text-align: right;
  }
  .person-name { font-size: 23px; font-weight: 700; letter-spacing: 0.3px; }
  .person-title { font-size: 15px; font-weight: 500; margin-top: 2px; }
  .divider {
    position: absolute; left: 256px; top: 88px; width: 1px; height: 96px;
    background: var(--on-green);
  }
  .contacts {
    position: absolute; left: 274px; top: 86px; list-style: none;
    font-size: 15px; line-height: 20px;
  }
  .contacts li { display: flex; align-items: center; gap: 10px; white-space: nowrap; }
  .contacts svg { width: 14px; height: 14px; flex: none; fill: var(--on-green); }
  .address {
    position: absolute; left: 0; right: 0; top: 228px; text-align: center;
    font-size: 15px; letter-spacing: 0.2px;
  }
</style>
</head>
<body>
<main class="sheet">
  <section class="card card-front">
    <div class="brand">
      <span class="brand-dot"></span>
      <span class="brand-name">
        <span class="line-main">T.K. Fenwick</span>
        <span class="line-sub">Manufacturing Company, Inc.</span>
      </span>
    </div>
    <p class="since">Since 1918</p>
    <p class="front-web">www.tkfenwick.example</p>
  </section>

  <section class="card card-back">
    <div class="person">
      <p class="person-name">Dale Fenwick</p>
      <p class="person-title">Vice President</p>
    </div>
    <span class="divider"></span>
    <ul class="contacts">
      <li><svg viewBox="0 0 24 24"><path d="M6.6 10.8a15 15 0 0 0 6.6 6.6l2.2-2.2c.3-.3.7-.4 1-.2 1.1.4 2.3.6 3.6.6.6 0 1 .4 1 1V20c0 .6-.4 1-1 1A17 17 0 0 1 3 4c0-.6.4-1 1-1h3.5c.6 0 1 .4 1 1 0 1.3.2 2.5.6 3.6.1.3 0 .7-.2 1z"/></svg>770 555 4821</li>
      <li><svg viewBox="0 0 24 24"><path d="M7 1h10a2 2 0 0 1 2 2v18a2 2 0 0 1-2 2H7a2 2 0 0 1-2-2V3a2 2 0 0 1 2-2zm0 3v14h10V4zm5 15.5a1 1 0 1 0 0 2 1 1 0 0 0 0-2z"/></svg>770 555 3067</li>
      <li><svg viewBox="0 0 24 24"><path d="M6 2h12v6H6zM4 9h16a2 2 0 0 1 2 2v7h-4v4H6v-4H2v-7a2 2 0 0 1 2-2zm4 7v4h8v-4z"/></svg>770 555 9144</li>
      <li><svg viewBox="0 0 24 24"><path d="M2 5h20v14H2zm2 2v.5l8 5 8-5V7zm0 2.8V17h16V9.8l-8 5z"/></svg>dale@tkfenwick.example</li>
      <li><svg viewBox="0 0 24 24"><path d="M12 2a10 10 0 1 0 0 20 10 10 0 0 0 0-20zm-1 17.9A8 8 0 0 1 4.1 11H7a14 14 0 0 0 4 8.9zM4.1 9A8 8 0 0 1 11 4.1 14 14 0 0 0 7 9zm8.9 10.9A14 14 0 0 0 17 11h2.9a8 8 0 0 1-6.9 8.9zM17 9a14 14 0 0 0-4-4.9A8 8 0 0 1 19.9 9z"/></svg>www.tkfenwick.example</li>
    </ul>
    <p class="address">4700 West Harbor Boulevard, Suite #150, Roswell, GA 30076</p>
  </section>
</main>
</body>
</html>
```